zAvora Corporate Website

zAvora is a well-funded start up developing an Online Marketing Platform for small businesses in Europe.
We are launching in February 2012 with all-in-one online marketing services including professional website, DIY SEO, Dashboard with Reports and Online marketing tools, and Support.
Our internal web designer has come up with a preliminary website design which we wish to continue to improve using new ideas, colours, layout, image, etc.
The brief is very simple - improve the website whether it is look & feel, ease of use, conversion rate - we are looking for overall improvements.
The contest will last 5 days and we will award the winner £300.
If you are the winner , you will also be required to provide designs for 3 more internal pages adhering to the proposed home page design.
Judging criteria : -
Visual Design
Layout must adhere to best practices and wire frame. If you decide to move elements around significantly please provide reason
Functional, informative and drives calls to action
Industry/Entity Type
Marketing
Look and feel
Each slider illustrates characteristics of the customer's brand and the style your logo design should communicate.

```html
<!DOCTYPE html>
<html lang="en">
<head>
<meta charset="utf-8">
<title>zAvora – Online Marketing for Small Business</title>
<link href="https://fonts.googleapis.com/css2?family=Open+Sans:wght@300;400;600;700&family=Oswald:wght@500;700&display=swap" rel="stylesheet">
<style>
:root{
  --orange:#f7941d;
  --orange-dark:#e9720c;
  --green:#6aa51c;
  --green-dark:#4f8512;
  --green-pale:#eef1e6;
  --ink:#222;
  --text:#555;
  --muted:#888;
  --line:#d8d8d8;
  --bg:#f5f5f3;
  --white:#fff;
  --tag:#2a5aa0;
}
*{box-sizing:border-box;margin:0;padding:0}
html,body{width:743px;height:1200px;overflow:hidden}
body{background:var(--bg);font-family:"Open Sans",Arial,sans-serif;color:var(--text);position:relative}
.abs{position:absolute}

/* top bar */
.topbar{left:0;top:0;width:743px;height:30px;background:linear-gradient(#fff,#ececec);border-bottom:1px solid #ddd}
.nav{left:104px;top:8px;display:flex;align-items:center;font-size:7px;color:#333;text-transform:uppercase}
.nav a{color:#333;text-decoration:none;padding:0 5px}
.nav .sep{color:#666}
.nav a.active{background:var(--orange);color:#fff;border-radius:2px;padding:4px 7px}
.search{left:482px;top:6px;width:162px;height:19px;background:#fff;border:1px solid #ccc}
.search svg{position:absolute;right:5px;top:3px}

/* brand */
.brand{left:106px;top:60px;display:flex;align-items:center;gap:6px}
.brand .dot{width:36px;height:36px;border-radius:50%;background:var(--orange)}
.brand .name{font-size:36px;font-weight:400;color:var(--ink);letter-spacing:-.5px}
.tagline{left:130px;top:126px;width:200px;font-size:14.5px;font-weight:300;color:var(--orange);line-height:1.25}
.checks{left:182px;top:174px;list-style:none}
.checks li{font-size:12.5px;font-weight:300;color:#555;height:21px;display:flex;align-items:center;gap:9px}
.cta{left:181px;top:266px;width:136px;height:48px;border-radius:5px;background:linear-gradient(#ffb02f,var(--orange-dark));border:1px solid #e28a0e;text-align:center;color:#fff}
.cta small{display:block;font-size:10.5px;margin-top:4px}
.cta strong{display:block;font-size:20px;font-weight:700;line-height:1.05}

/* hero */
.hero-photo{left:352px;top:196px;width:250px;height:140px;border-radius:4px;background:linear-gradient(160deg,#e9e9e7 0%,#d6d8d3 55%,#c9ccc6 100%)}
.tag{position:absolute;font-size:6.4px;font-weight:600;color:var(--tag);background:#fff;border:1px solid #b8cbe3;padding:2px 6px;white-space:nowrap}

/* features */
.features{left:93px;top:353px;width:557px;height:112px;background:var(--green-pale);border:1px solid #e0e4d8}
.card{position:absolute;top:25px;width:127px;height:58px;background:#f6f7f2;border-radius:3px;display:flex;gap:6px;padding:8px 5px}
.card h3{font-size:11.5px;font-weight:400;color:var(--green);margin-bottom:2px}
.card p{font-size:6.2px;line-height:1.35;color:#555}

/* ribbon */
.ribbon{left:40px;top:464px;width:662px;height:78px}
.ribbon-text{left:86px;top:482px;width:572px;text-align:center;color:#fff}
.ribbon-text h2{font-size:16px;font-weight:300;letter-spacing:-.2px}
.ribbon-text h2 b{font-weight:400}
.ribbon-text p{font-size:11.5px;font-weight:300;margin-top:0}

/* about */
.about{left:104px;top:556px;width:536px}
.about h2{font-size:16px;font-weight:400;color:var(--ink);margin-bottom:9px}
.about p{font-size:6.7px;line-height:10.4px;color:#444;margin-bottom:10.4px}
.about em{font-style:normal;color:var(--orange)}

/* packages */
.packages{left:93px;top:722px;width:557px;height:99px;background:#e6e6e4;border-radius:3px}
.pkg{position:absolute;top:6px;width:128px;height:86px;overflow:hidden;color:#fff;font-family:"Oswald",Arial,sans-serif;padding:8px 10px}
.pkg .l1{font-size:16px;line-height:1;font-weight:700}
.pkg .l2{font-size:19px;line-height:1.05;font-weight:700}
.pkg .l3{font-family:"Open Sans",Arial,sans-serif;font-size:6.5px;font-weight:700}
.pkg.green .l1{font-size:13.5px;line-height:1.1}
.pkg .foot{position:absolute;left:0;right:0;bottom:0;height:18px;background:rgba(0,0,0,.35);text-align:center;font-family:"Open Sans",Arial,sans-serif;font-size:7.5px;line-height:18px}
.pkg .band{position:absolute;right:-24px;top:8px;width:80px;height:13px;transform:rotate(45deg);background:#c81616;text-align:center;font-size:7.5px;line-height:13px;font-weight:700}
.pkg.red{left:5px;background:linear-gradient(#e23125,#a9130e)}
.pkg.orange{left:143px;background:linear-gradient(#f7a40f,#d8540a)}
.pkg.green{left:279px;background:linear-gradient(#5cb52a,#2d7f12)}
.pkg.red .band{background:#1f63b8}
.how{left:518px;top:734px;width:124px}
.how h4{font-family:"Oswald",Arial,sans-serif;font-size:10px;font-weight:500;color:var(--green);margin-bottom:6px}
.how p{font-size:6.5px;line-height:10.4px;color:#444;text-align:justify}

/* examples */
.examples{left:117px;top:868px;width:150px}
.examples h3{font-size:10px;font-weight:400;color:var(--ink);line-height:1.3;margin-bottom:10px}
.examples p{font-size:6.8px;line-height:10.4px;color:var(--muted);text-align:justify;width:124px}
.more{left:192px;top:965px;font-size:6.8px;color:var(--orange);display:flex;gap:4px;align-items:center}
.slide{position:absolute;top:864px;height:104px}
.slide.side{background:linear-gradient(#e9e9e9,#cfd3d8)}
.slide.main{left:350px;top:860px;width:188px;height:112px;border:3px solid var(--green);background:linear-gradient(#1d1d1d 0 12%,#f3f3f3 12% 55%,#dcdcdc 55%)}

/* footer */
.footer{left:0;top:1018px;width:743px;height:182px;background:#ececea;border-top:2px solid var(--green)}
.flogo{left:91px;top:1020px;width:102px;height:45px;background:var(--green);display:flex;align-items:center;justify-content:center;gap:5px}
.flogo .dot{width:16px;height:16px;border-radius:50%;background:#2b4d0c}
.flogo span{font-size:17px;color:#2b4d0c}
.fhead{position:absolute;top:1044px;display:flex;align-items:center;gap:10px;font-size:12px;color:#333}
.flist{position:absolute;top:1076px;list-style:none}
.flist li{font-size:7px;color:#777;height:17.5px;padding-left:7px;position:relative}
.flist li::before{content:"";position:absolute;left:0;top:3px;border:2px solid transparent;border-left:3px solid var(--green)}
.follow{left:102px;top:1079px;font-size:11px;color:#333}
.social{position:absolute;top:1097px;width:16px;height:16px;border-radius:50%;background:#fff;border:1px solid #ddd}
.email{left:553px;top:1077px;width:73px;height:15px;background:#fff;border:1px solid #ddd;font-size:6.5px;color:#aaa;font-style:italic;padding:3px 4px}
.plus{left:630px;top:1077px;width:16px;height:15px;background:var(--green);color:#fff;font-weight:700;font-size:12px;text-align:center;line-height:14px}
.like{left:556px;top:1100px;width:10px;height:10px;background:#5b74a8}
.count{left:582px;top:1099px;font-size:6.5px;border:1px solid #ccc;background:#fff;padding:0 3px}
.copy{left:0;top:1167px;width:743px;text-align:center;font-size:6.8px;color:#777}
</style>
</head>
<body>

<header>
  <div class="abs topbar"></div>
  <nav class="abs nav">
    <a class="active">Home</a><span class="sep">|</span>
    <a>About us</a><span class="sep">|</span>
    <a>Quick tour</a><span class="sep">|</span>
    <a>Pricing</a><span class="sep">|</span>
    <a>Contact us</a><span class="sep">|</span>
    <a>Login</a>
  </nav>
  <div class="abs search"><svg width="14" height="13" viewBox="0 0 14 13"><circle cx="5.5" cy="5.5" r="4" fill="none" stroke="#f39a16" stroke-width="2"/><line x1="8.5" y1="8.5" x2="13" y2="12" stroke="#f39a16" stroke-width="2.5"/></svg></div>
</header>

<section class="hero">
  <div class="abs brand"><span class="dot"></span><span class="name">zAvora</span></div>
  <p class="abs tagline">Getting a website has never been so simple</p>
  <ul class="abs checks">
    <li><svg width="10" height="9" viewBox="0 0 10 9"><path d="M1 5l3 3 5-7" fill="none" stroke="#6aa51c" stroke-width="2"/></svg>Business Websites</li>
    <li><svg width="10" height="9" viewBox="0 0 10 9"><path d="M1 5l3 3 5-7" fill="none" stroke="#6aa51c" stroke-width="2"/></svg>Online Marketing</li>
    <li><svg width="10" height="9" viewBox="0 0 10 9"><path d="M1 5l3 3 5-7" fill="none" stroke="#6aa51c" stroke-width="2"/></svg>Dashboard Controls</li>
    <li><svg width="10" height="9" viewBox="0 0 10 9"><path d="M1 5l3 3 5-7" fill="none" stroke="#6aa51c" stroke-width="2"/></svg>Full Setup &amp; Support</li>
  </ul>
  <a class="abs cta"><small>Sign up NOW for</small><strong>FREE!</strong></a>

  <div class="abs hero-photo" role="img" aria-label="Photo of a thoughtful businessman looking up at marketing topics"></div>
  <div class="tag" style="left:376px;top:70px">PPC</div>
  <div class="tag" style="left:438px;top:80px">Testimonials</div>
  <div class="tag" style="left:509px;top:74px">Deals</div>
  <div class="tag" style="left:556px;top:85px">Hosting</div>
  <div class="tag" style="left:377px;top:99px">Email Marketing</div>
  <div class="tag" style="left:500px;top:99px">SEO</div>
  <div class="tag" style="left:568px;top:102px">Content Management</div>
  <div class="tag" style="left:438px;top:109px">Images</div>
  <div class="tag" style="left:524px;top:117px">Web Design</div>
  <div class="tag" style="left:410px;top:122px">Klarvo Ads</div>
  <div class="tag" style="left:355px;top:136px">Directories</div>
  <div class="tag" style="left:550px;top:138px">Reporting</div>
  <div class="tag" style="left:413px;top:150px">Blog / News</div>
  <div class="tag" style="left:562px;top:158px">Chirplet Feeds</div>
  <div class="tag" style="left:392px;top:177px">Friendloop</div>
  <div class="tag" style="left:558px;top:182px">Referals</div>
</section>

<section class="abs features">
  <div class="card" style="left:6px">
    <svg width="26" height="26" viewBox="0 0 26 26"><rect x="2" y="6" width="5" height="18" fill="#8a8a8a"/><rect x="9" y="13" width="5" height="11" fill="#8a8a8a"/><rect x="16" y="17" width="6" height="7" fill="#8a8a8a"/><rect x="1" y="23" width="24" height="2" fill="#666"/></svg>
    <div><h3>Case Studies</h3><p>Read real stories about small businesses online</p></div>
  </div>
  <div class="card" style="left:145px">
    <svg width="26" height="26" viewBox="0 0 26 26"><circle cx="13" cy="10" r="7" fill="none" stroke="#8a8a8a" stroke-width="2"/><rect x="10" y="17" width="6" height="5" fill="#8a8a8a"/></svg>
    <div><h3>How to</h3><p>Learn from our online marketing tips for small business</p></div>
  </div>
  <div class="card" style="left:284px">
    <svg width="26" height="26" viewBox="0 0 26 26"><path d="M2 4h16v11H8l-4 4v-4H2z" fill="#7a7a7a"/><path d="M10 11h14v10h-2v4l-4-4h-8z" fill="#9a9a9a"/></svg>
    <div><h3>News &amp; Chatter</h3><p>Get up-to-date news and chatter about online marketing</p></div>
  </div>
  <div class="card" style="left:423px">
    <svg width="26" height="26" viewBox="0 0 26 26"><circle cx="13" cy="15" r="10" fill="#8a8a8a"/><rect x="11" y="2" width="4" height="3" fill="#8a8a8a"/><line x1="13" y1="15" x2="13" y2="8" stroke="#fff" stroke-width="2"/></svg>
    <div><h3>Demo</h3><p>Find out what zAvora can do for your business.</p></div>
  </div>
</section>

<svg class="abs ribbon" viewBox="0 0 662 78" aria-hidden="true">
  <polygon points="0,10 56,10 56,70 0,70 20,40" fill="#5a9416"/>
  <polygon points="662,10 606,10 606,70 662,70 642,40" fill="#5a9416"/>
  <polygon points="46,62 56,70 46,70" fill="#3b6c0c"/>
  <polygon points="616,62 606,70 616,70" fill="#3b6c0c"/>
  <rect x="46" y="0" width="570" height="70" fill="#6aa51c"/>
  <rect x="50" y="4" width="562" height="62" fill="none" stroke="#9fd05a" stroke-dasharray="2 2"/>
</svg>
<div class="abs ribbon-text">
  <h2>The Complete Online Marketing Solution for <b>Small Business Websites</b></h2>
  <p>“Get a big online presence and more sales leads in 30 minutes”</p>
</div>

<section class="abs about">
  <h2>About Us</h2>
  <p><em>zAvora</em> will build your business website, optimise SEO marketing and make recommendations on best practices to help you win customers. Let our team of experts design a business website for you. Choose a business website from <em>zAvora's</em> broad array of fabulous, customisable business websites and our experts will have your business online in minutes. <em>zAvora</em> lets you create a professional business website without the need to know how to code or programme.</p>
  <p>Your business website comes with automatic Internet marketing, marketing on the Internet is easy with <em>zAvora</em>, we automatically optimise your site for SEO marketing and we can run Klarvo ad campaigns when you need them. Get a business website with online marketing now. <em>zAvora</em> brings your Small Business Website to LIFE!</p>
  <p>View our example business websites above, watch the video demo to see how to make a business website or call us now and get your business marketing online today. The <em>zAvora</em> website builder gives you a professional online appearance - post your own images, give customers your latest news and create customer testimonials, it's the most complete online marketing solution for your business.</p>
</section>

<section class="abs packages">
  <div class="pkg red"><div class="l1">Free</div><div class="l2">SETUP</div><div class="band">£199</div><div class="foot">WEB OFFER ONLY</div></div>
  <div class="pkg orange"><div class="l1">Pro</div><div class="l2">PACKAGE</div><div class="l3">Big online presence</div><div class="band">£22</div><div class="foot">Business Website &amp; Easy Dashboard</div></div>
  <div class="pkg green"><div class="l1">TURBO SALES</div><div class="l1">PRO PLUS</div><div class="l3">More sales LEADS</div><div class="band">£29</div><div class="foot" style="height:22px;line-height:10px;padding-top:1px">Business Website,<br>Easy Dashboard &amp; ppc Sales</div></div>
</section>
<div class="abs how">
  <h4>How does it work?</h4>
  <p>Neque porro quisquam est qui dolorem ipsum quia dolor vel eum iriure dolor in hendrerit in vulputate velit dou site vesse molestie consequat, vel illumsit amet, adipisci velit"</p>
</div>

<section>
  <div class="abs examples">
    <h3>View examples of our<br>stunning business websites</h3>
    <p>Duis autem vel eum iriure dolor in hendrerit in vulputate velit esse molestie consequat, vel illum dolore eu feugiat nulla facilisis at vero eros et accumsan. esse molestie.</p>
  </div>
  <a class="abs more"><svg width="8" height="8" viewBox="0 0 8 8"><circle cx="4" cy="4" r="3.4" fill="none" stroke="#f7941d" stroke-width=".8"/><path d="M3 2.3l2 1.7-2 1.7z" fill="#f7941d"/></svg>View more</a>
  <svg class="abs" style="left:278px;top:896px" width="12" height="26" viewBox="0 0 12 26"><path d="M12 0v26L0 13z" fill="#8a8a8a"/></svg>
  <svg class="abs" style="left:602px;top:896px" width="12" height="26" viewBox="0 0 12 26"><path d="M0 0v26l12-13z" fill="#f7941d"/></svg>
  <div class="slide side" style="left:310px;width:42px" role="img" aria-label="Screenshot of an example business website"></div>
  <div class="slide side" style="left:538px;width:48px;background:linear-gradient(#1b1b1b 0 20%,#2a5ea8 20% 70%,#eee 70%)" role="img" aria-label="Screenshot of an example business website"></div>
  <div class="slide main" role="img" aria-label="Screenshot of the Vexlo example business website"></div>
</section>

<footer>
  <div class="abs footer"></div>
  <div class="abs flogo"><span class="dot"></span><span>zAvora</span></div>
  <div class="abs follow">Follow</div>
  <span class="social" style="left:104px"></span>
  <span class="social" style="left:132px"></span>
  <span class="social" style="left:160px"></span>

  <div class="fhead" style="left:206px"><svg width="18" height="18" viewBox="0 0 18 18"><circle cx="9" cy="9" r="6" fill="none" stroke="#777" stroke-width="4" stroke-dasharray="3 2"/><circle cx="9" cy="9" r="2.5" fill="#777"/></svg>OurServices</div>
  <div class="fhead" style="left:344px"><svg width="20" height="22" viewBox="0 0 20 22"><rect x="1" y="1" width="18" height="20" rx="3" fill="none" stroke="#777" stroke-width="2"/><rect x="4" y="4" width="12" height="12" fill="#bbb"/></svg>ContactUs</div>
  <div class="fhead" style="left:446px"><svg width="26" height="18" viewBox="0 0 26 18"><path d="M1 2h9l2 3h13v12H1z" fill="#777"/></svg>Navigation</div>
  <div class="fhead" style="left:552px"><svg width="26" height="18" viewBox="0 0 26 18"><rect x="1" y="1" width="24" height="16" fill="#888"/><path d="M1 1l12 9 12-9" fill="none" stroke="#eee" stroke-width="1.5"/></svg>Subscribe</div>

  <ul class="flist" style="left:205px"><li>Search Engine Optimization (SEO)</li><li>Social Media</li><li>Web Analytics</li></ul>
  <ul class="flist" style="left:343px"><li>Contact Us</li><li>Customer Support</li><li>Request a call back</li><li>FAQ's</li></ul>
  <ul class="flist" style="left:447px"><li>Site Map</li><li>Terms and Condition</li><li>Privacy &amp; Policy</li><li>Get in Touch</li></ul>

  <div class="abs email">Type your email here</div>
  <div class="abs plus">+</div>
  <span class="abs like"></span>
  <span class="abs" style="left:568px;top:1100px;font-size:6.5px;color:#3b5998">Like</span>
  <span class="abs count">62</span>

  <p class="abs copy">Copyright © 2011 zAvora Pvt. Ltd 2011 - All rights reserved. Managed by zAvora &nbsp;|&nbsp; Admin</p>
</footer>

</body>
</html>
```